Dietitian needs awesome business card

I need a contemporary design that's eye catching but professional.
My card is to given to doctors, specialists and patients alike.
I manage patients with chronic diseases
I have uploaded my logo and current business card, I would also like the other Certified Clinical Nutritionist logo incorporated into the design

Target Market(s)

Doctors, specialists and patients

Industry/Entity Type

Healthcare

Contact Information for Business Card

www.brightfieldnutrition.com.au
Ph: 0427 561 903
Fax: 6457 2183
email: marcus.k.diet@fernmail.com
Space on the back of the card with: Appointment date, Appointment time and appointment location

Font styles to use
Serif

Colors
fbee3e
876aae
ffc214

Requirements
Must have
• My Logo
• Certified Clinical Nutritionist Logo
• My 4 locations - Pinebrook Medical Centre, North Corrin Health, Hollis Medical, Ashcombe Doctors Surgery
Nice to have
• I like the colours in my current business card

```html
<!DOCTYPE html>
<html lang="en">
<head>
<meta charset="utf-8">
<title>Brightfield Nutrition &amp; Dietetics – Business Card</title>
<link rel="stylesheet" href="https://fonts.googleapis.com/css2?family=Libre+Franklin:wght@400;500;600&display=swap">
<style>
  :root {
    --stage: #2b2b2b;
    --card: #ffffff;
    --navy: #1f2a8c;
    --blue: #1b5fb0;
    --orange: #f26b1d;
    --green: #7ab51d;
    --ink: #4a4a4a;
    --rule: #c9cccf;
    --wash-a: #f4f6f1;
    --wash-b: #e3e9dc;
  }
  * { box-sizing: border-box; margin: 0; padding: 0; }
  html, body { width: 1200px; height: 987px; overflow: hidden; }
  body {
    background: var(--stage);
    font-family: "Libre Franklin", Arial, sans-serif;
    position: relative;
  }
  .card {
    position: absolute;
    left: 293px;
    width: 615px;
    height: 350px;
    border-radius: 21px;
    background: var(--card);
    box-shadow: 0 4px 10px rgba(0,0,0,.45);
    overflow: hidden;
  }
  .card--front { top: 129px; }
  .card--back { top: 507px; }

  /* Front */
  .brand {
    position: absolute; left: 36px; top: 50px;
    display: flex; align-items: center; gap: 14px;
  }
  .brand__dot {
    width: 52px; height: 52px; border-radius: 50%;
    background: var(--green);
  }
  .brand__name {
    font-size: 24px; font-weight: 500; color: var(--navy);
    line-height: 1.15; width: 250px;
  }
  .person { position: absolute; left: 36px; top: 219px; }
  .person__name { font-size: 22px; font-weight: 600; color: var(--navy); margin-bottom: 4px; }
  .person__role { font-size: 16.5px; line-height: 23px; }
  .person__role--primary { color: var(--orange); }
  .person__role--secondary { color: var(--green); }
  .contacts {
    position: absolute; left: 317px; top: 220px;
    list-style: none;
  }
  .contacts li {
    display: flex; align-items: center; gap: 10px;
    font-size: 16.5px; color: var(--ink); height: 23.5px;
  }
  .contacts svg { width: 17px; height: 17px; fill: var(--navy); flex: none; }

  /* Back */
  .back__wash {
    position: absolute; inset: 0;
    background: radial-gradient(ellipse at 40% 35%, var(--wash-b), var(--wash-a) 60%, #fbfcfa);
    opacity: .85;
  }
  .appointment { position: absolute; inset: 0; }
  .appointment__title {
    position: absolute; top: 30px; width: 100%; text-align: center;
    font-size: 20px; font-weight: 600; color: var(--navy);
  }
  .appointment__line {
    position: absolute; left: 42px; width: 530px; height: 1px; background: var(--rule);
  }
  .appointment__when {
    position: absolute; left: 42px; top: 224px; width: 530px;
    display: flex; align-items: baseline; font-size: 17px; color: var(--navy);
  }
  .appointment__fill {
    border-bottom: 1.5px dotted var(--navy); margin: 0 8px; height: 14px;
  }
  .appointment__ampm { font-size: 13px; }
  .locations {
    position: absolute; left: 43px; top: 266px; width: 540px;
    display: grid; grid-template-columns: 305px 1fr; row-gap: 7px;
    list-style: none;
  }
  .locations li {
    display: flex; align-items: center; gap: 6px;
    font-size: 16.5px; color: var(--ink);
  }
  .locations li::before {
    content: ""; width: 13px; height: 13px; border: 1.5px solid var(--navy); flex: none;
  }
</style>
</head>
<body>

<section class="card card--front">
  <div class="brand">
    <span class="brand__dot"></span>
    <span class="brand__name">Brightfield Nutrition &amp; Dietetics</span>
  </div>
  <div class="person">
    <p class="person__name">Marcus Kellaway</p>
    <p class="person__role person__role--primary">Certified Clinical Nutritionist</p>
    <p class="person__role person__role--secondary">Nutritionist &amp; Chef</p>
  </div>
  <ul class="contacts">
    <li><svg viewBox="0 0 24 24"><path d="M6.6 10.8a15.1 15.1 0 0 0 6.6 6.6l2.2-2.2c.3-.3.7-.4 1-.2 1.1.4 2.3.6 3.6.6.6 0 1 .4 1 1V20c0 .6-.4 1-1 1C10.6 21 3 13.4 3 4c0-.6.4-1 1-1h3.5c.6 0 1 .4 1 1 0 1.3.2 2.5.6 3.6.1.3 0 .7-.2 1z"/></svg>0427 561 903</li>
    <li><svg viewBox="0 0 24 24"><path d="M7 3h10v5H7zM4 9h16a2 2 0 0 1 2 2v6h-4v4H6v-4H2v-6a2 2 0 0 1 2-2zm4 7v3h8v-3z"/></svg>6457 2183</li>
    <li><svg viewBox="0 0 24 24"><path d="M3 5h18v14H3zm2 2v.5l7 4.5 7-4.5V7zm0 2.8V17h14V9.8l-7 4.5z"/></svg>marcus.k.diet@fernmail.com</li>
    <li><svg viewBox="0 0 24 24"><path d="M12 2a10 10 0 1 0 0 20 10 10 0 0 0 0-20zm-1 17.9A8 8 0 0 1 4.2 10.6L9 15.4v1a2 2 0 0 0 2 2zm6.9-2.5a2 2 0 0 0-1.9-1.4h-1v-3a1 1 0 0 0-1-1H8v-2h2a1 1 0 0 0 1-1V7h2a2 2 0 0 0 2-2v-.4a8 8 0 0 1 2.9 12.8z"/></svg>brightfieldnutrition.com.au</li>
  </ul>
</section>

<section class="card card--back">
  <div class="back__wash" role="img" aria-label="Faded photograph of fresh green vegetables and herbs"></div>
  <div class="appointment">
    <h2 class="appointment__title">YOUR APPOINTMENT</h2>
    <span class="appointment__line" style="top:84px"></span>
    <span class="appointment__line" style="top:119px"></span>
    <span class="appointment__line" style="top:154px"></span>
    <span class="appointment__line" style="top:189px"></span>
    <div class="appointment__when">
      <span>Date :</span><span class="appointment__fill" style="width:214px"></span>
      <span>Time :</span><span class="appointment__fill" style="width:136px"></span>
      <span class="appointment__ampm">AM/PM</span>
    </div>
    <ul class="locations">
      <li>Pinebrook Medical Centre</li>
      <li>Hollis Medical</li>
      <li>North Corrin Health</li>
      <li>Ashcombe Doctors Surgery</li>
    </ul>
  </div>
</section>

</body>
</html>
```